Wordpress website for a new Podcast

Hi, We are looking for a designer to create a wordpress website project for a new podcast and publish it on the domain we own.

The show is called “Bright Gatherings” (logo included) and its aim is to interview guests who work as professional facilitators, trainers, teachers and coaches. The show has a positive vibe, is fun, vibrant and full of positive energy. These are the feelings we want to convey in the design.

The website should have a similar structure to: https://www.plumvesselcast.example/ with the following content:

1) The main page including:
- navigation bar and social buttons at the top
- main graphic design featuring the latest episode
- "latest episodes" section displaying 3 episodes (please design a mask to be used for new episodes when they air together with the face of the interviewee) -> this will link to the respective episodes
- please design an "bright gatherings" book cover mockup to be inluded as a banner -> this will link to Orindel
- subscribe to the newsletter - a banner capturing the name and email of the user -> to be connected to PostWren.
-> a working episode search.

2) Episodes page
- the show will be divided into seasons (12 episodes each) and each episode will need a separate "blog entry" including:
-> A short article (4-5 paragraphs) + stock image
-> interviewee's bio and social links

3) Meet the hosts page
- including bios of the two hosts of the show
- links to their social profiles
- a "request speaker availability" form which sends an email

Some additional nice-to-haves:
1) Good and clean Bio's would be awesome (both for the hosts & the interviewees),
2) an easily navigable episode system,
3) a keyword/date search option
4) easy to share options (share to WhatsApp, Facebook, Twitter, LinkedIn) 5) We must be able to track how the podcasts are shared (google analytics?)

```html
<!DOCTYPE html>
<html lang="en">
<head>
<meta charset="utf-8">
<title>Bright Gatherings — Podcast</title>
<link rel="stylesheet" href="https://fonts.googleapis.com/css2?family=Montserrat:ital,wght@0,400;0,500;0,600;0,700;0,800;1,400&family=Raleway:ital,wght@0,400;0,500;0,700;1,400&display=swap">
<style>
:root{
  --orange:#f0581f;
  --orange-hot:#ff6a10;
  --orange-deep:#e63d0b;
  --yellow:#ffb400;
  --ink:#111111;
  --text:#2b2b2b;
  --muted:#555555;
  --grey:#d8d8d8;
  --white:#ffffff;
  --hero-dark:#3c4048;
  --band-dark:#1e1a17;
  --star:#f7b500;
}
*{box-sizing:border-box;margin:0;padding:0}
html,body{width:1200px;height:4079px;overflow:hidden}
body{position:relative;background:var(--white);font-family:"Raleway",sans-serif;color:var(--text)}
.abs{position:absolute}

/* header */
.site-header{position:absolute;left:0;top:0;width:1200px;height:112px;background:var(--orange)}
.brand-box{position:absolute;left:111px;top:0;width:111px;height:108px;background:var(--orange-hot);display:flex;align-items:center;justify-content:center;text-align:center;font-family:"Montserrat",sans-serif;font-weight:800;font-size:15px;line-height:1.1;color:var(--ink);text-transform:uppercase}
.social{position:absolute;top:13px;left:527px;display:flex;gap:26px}
.social span{width:22px;height:22px;border:2px solid var(--white);border-radius:4px;display:block}
.book-tab{position:absolute;left:807px;top:0;width:206px;height:40px;background:var(--ink);clip-path:polygon(7% 0,100% 0,93% 100%,0 100%);color:var(--white);font-family:"Montserrat",sans-serif;font-weight:700;font-size:15px;display:flex;align-items:center;justify-content:center}
.search-icon{position:absolute;left:1042px;top:10px}
.main-nav{position:absolute;top:68px;left:0;width:1200px;font-family:"Montserrat",sans-serif;font-weight:600;font-size:15px;color:var(--white)}
.main-nav a{position:absolute;color:var(--white);text-decoration:none;white-space:nowrap}
.main-nav a.active{color:var(--ink);text-decoration:underline}

/* hero */
.hero{position:absolute;left:0;top:112px;width:1200px;height:585px;background:linear-gradient(135deg,#5b5f66 0%,var(--hero-dark) 45%,#6e6a63 100%)}
.hero-wave{position:absolute;left:0;top:0}
.hero-title{position:absolute;left:111px;top:112px;font-family:"Montserrat",sans-serif;font-weight:700;font-size:51px;color:var(--white);letter-spacing:.5px}
.hero-lede{position:absolute;left:111px;top:186px;width:620px;font-size:20px;line-height:26px;color:var(--white)}
.pill{position:absolute;height:41px;border-radius:21px;background:var(--ink);color:var(--white);font-family:"Montserrat",sans-serif;font-weight:700;font-size:16px;display:flex;align-items:center;justify-content:center}
.book-mockup{position:absolute;left:741px;top:91px;width:367px;height:406px;background:linear-gradient(135deg,#f4f4f4,#cfcfcf);box-shadow:0 10px 30px rgba(0,0,0,.4)}
.book-mockup .cover{position:absolute;left:40px;top:30px;right:22px;bottom:62px;background:radial-gradient(circle at 50% 45%,var(--yellow),var(--orange-hot) 55%,var(--orange-deep))}

/* section heads */
.bar{position:absolute;height:6px;background:var(--orange);border-radius:3px}
.section-title{position:absolute;font-family:"Montserrat",sans-serif;font-weight:700;color:var(--ink)}

/* episodes */
.episode-card{position:absolute;top:855px;width:268px;height:451px;background:var(--white);box-shadow:0 3px 8px rgba(0,0,0,.2);text-align:center}
.episode-card .photo{height:147px;background:linear-gradient(180deg,#bdbdbd,#8d8d8d)}
.episode-card .num{margin-top:28px;font-size:13px;color:var(--ink)}
.episode-card h3{margin:10px auto 0;width:200px;font-family:"Montserrat",sans-serif;font-weight:700;font-size:17px;line-height:20px;color:var(--ink)}
.episode-card p{position:absolute;left:40px;width:188px;top:278px;font-size:15px;line-height:26px;text-align:justify;text-align-last:justify;color:var(--muted)}
.episode-card .explore{position:absolute;left:47px;top:397px;width:175px;height:29px;background:var(--ink);color:var(--white);font-size:15px;display:flex;align-items:center;justify-content:center}
.arrow{position:absolute;top:1028px}

/* about */
.about-bg{position:absolute;left:0;top:1361px}
.about-text{position:absolute;left:111px;top:1559px;width:483px;font-size:13.5px;line-height:28.3px;text-align:justify;color:var(--muted)}
.round-photo{position:absolute;border-radius:50%}

/* hosts */
.hosts-text{position:absolute;left:601px;top:2285px;width:491px;font-family:"Montserrat",sans-serif;font-weight:600;font-size:13.5px;line-height:25px;text-align:justify;color:var(--ink)}

/* newsletter */
.newsletter{position:absolute;left:0;top:2664px;width:1200px;height:268px;background:linear-gradient(90deg,#2a2521,var(--band-dark) 50%,#141210)}
.newsletter h2{position:absolute;left:111px;top:72px;width:620px;font-family:"Montserrat",sans-serif;font-weight:700;font-size:20px;line-height:29px;color:var(--white);text-transform:uppercase}
.field{position:absolute;top:162px;height:25px;border-radius:13px;font-size:13.5px;color:var(--white);display:flex;align-items:center;justify-content:center}
.field.input{background:#3a3633}
.field.submit{border:2px solid var(--white)}
.logo-panel{position:absolute;left:765px;top:2664px;width:324px;height:326px;background:radial-gradient(circle at 50% 50%,var(--yellow),var(--orange-hot) 55%,var(--orange-deep));display:flex;align-items:center;justify-content:center;text-align:center;font-family:"Montserrat",sans-serif;font-weight:800;font-size:44px;line-height:1.1;color:var(--ink);text-transform:uppercase}

/* testimonials */
.testimonial{position:absolute;top:3198px;width:469px;height:395px;background:var(--white);border-radius:12px;box-shadow:0 3px 10px rgba(0,0,0,.18)}
.testimonial .stars{position:absolute;left:50px;top:32px;font-size:26px;letter-spacing:3px;color:var(--star)}
.testimonial .quote{position:absolute;left:33px;top:88px;font-family:"Montserrat",sans-serif;font-weight:800;font-size:30px;color:#333}
.testimonial p{position:absolute;left:63px;top:130px;width:378px;font-style:italic;font-size:14.5px;line-height:25.7px;color:var(--muted)}
.testimonial .tail{position:absolute;left:48px;top:395px}

/* footer */
.site-footer{position:absolute;left:0;top:3717px;width:1200px;height:362px;background:#000}
.footer-logo{position:absolute;left:522px;top:3684px;width:156px;height:155px;background:radial-gradient(circle,var(--yellow),var(--orange-hot) 55%,var(--orange-deep));display:flex;align-items:center;justify-content:center;text-align:center;font-family:"Montserrat",sans-serif;font-weight:800;font-size:21px;line-height:1.1;color:var(--ink);text-transform:uppercase}
.footer-nav a{position:absolute;top:3886px;font-family:"Montserrat",sans-serif;font-weight:700;font-size:27px;color:var(--white);text-decoration:none}
.footer-nav i{position:absolute;top:3882px;width:3px;height:36px;background:var(--white)}
.footer-note{position:absolute;left:270px;top:3945px;width:660px;text-align:center;font-size:14px;line-height:16px;color:#cfcfcf}
.copyright{position:absolute;left:0;top:4018px;width:1200px;text-align:center;font-family:"Montserrat",sans-serif;font-size:20px;color:var(--white)}
</style>
</head>
<body>

<header class="site-header">
  <div class="brand-box">Bright<br>Gatherings</div>
  <div class="social"><span></span><span></span><span></span><span></span><span></span></div>
  <div class="book-tab">GET THE BOOK</div>
  <svg class="search-icon" width="24" height="24" viewBox="0 0 24 24"><circle cx="10" cy="10" r="7" fill="none" stroke="#fff" stroke-width="3"/><line x1="15" y1="15" x2="22" y2="22" stroke="#fff" stroke-width="3"/></svg>
  <nav class="main-nav">
    <a class="active" style="left:396px">HOME</a>
    <a style="left:483px">ABOUT US</a>
    <a style="left:603px">EPISODES PAGE</a>
    <a style="left:766px">MEET THE HOSTS PAGE</a>
    <a style="left:988px">CONTACT US</a>
  </nav>
</header>

<section class="hero">
  <div class="abs" role="img" aria-label="Overhead photo of a team meeting around a wooden table with laptops" style="inset:0"></div>
  <svg class="hero-wave" width="1200" height="585" viewBox="0 0 1200 585"><path d="M0 505 C60 420 180 390 300 400 C470 415 520 540 780 560 C960 575 1110 565 1200 575 L1200 585 L0 585 Z" fill="#fff"/></svg>
  <h1 class="hero-title">BRIGHT GATHERINGS</h1>
  <p class="hero-lede">Lorem ipsum dolor sit amet, consectetur adipiscing elit, sed do eiusmod tempor incididunt ut labore et ultrices</p>
  <div class="pill" style="left:111px;top:274px;width:134px">READ MORE</div>
  <div class="book-mockup" role="img" aria-label="Book cover mockup for Bright Gatherings"><div class="cover"></div></div>
</section>

<div class="bar" style="left:325px;top:730px;width:546px"></div>
<h2 class="section-title" style="left:0;top:742px;width:1200px;text-align:center;font-size:41px">LATEST EPISODE PODCASTE</h2>

<svg class="arrow" style="left:54px" width="24" height="36" viewBox="0 0 24 36"><path d="M20 3 L5 18 L20 33" fill="none" stroke="#111" stroke-width="4"/></svg>
<svg class="arrow" style="left:1120px" width="24" height="36" viewBox="0 0 24 36"><path d="M4 3 L19 18 L4 33" fill="none" stroke="#111" stroke-width="4"/></svg>

<article class="episode-card" style="left:108px">
  <div class="photo" role="img" aria-label="Portrait of the episode 165 guest"></div>
  <div class="num">Episode 165:</div>
  <h3>Stop Apologizing for Your Core Focus | Marta Quillon</h3>
  <p>Lorem ipsum dolor amet, adipiscing elit, sed do eiusmod incididunt ut labore et dolore magna</p>
  <div class="explore">EXPLORE</div>
</article>
<article class="episode-card" style="left:467px">
  <div class="photo" role="img" aria-label="Portrait of the episode 166 guest"></div>
  <div class="num">Episode 166:</div>
  <h3>Demystifying What It Means to Live The Core Focus | Liora</h3>
  <p>Lorem ipsum dolor amet, adipiscing elit, sed do eiusmod incididunt ut labore et dolore magna</p>
  <div class="explore">EXPLORE</div>
</article>
<article class="episode-card" style="left:826px">
  <div class="photo" role="img" aria-label="Portrait of the episode 167 guest"></div>
  <div class="num">Episode 167:</div>
  <h3 style="margin-top:14px">Find Your Focus, Cut Your Stress | Dorian Vesk</h3>
  <p>Lorem ipsum dolor amet, adipiscing elit, sed do eiusmod incididunt ut labore et dolore magna</p>
  <div class="explore">EXPLORE</div>
</article>

<svg class="about-bg" width="1200" height="741" viewBox="0 0 1200 741"><path d="M0 32 C120 0 320 -10 520 20 C760 60 880 180 1000 190 C1100 198 1160 170 1200 150 L1200 741 L0 741 Z" fill="#d8d8d8"/></svg>
<div class="bar" style="left:109px;top:1452px;width:208px"></div>
<h2 class="section-title" style="left:110px;top:1470px;font-size:44px">ABOUT US</h2>
<p class="about-text">Lorem ipsum dolor sit amet, consectetur adipiscing elit, sed do eiusmod tempor incididunt ut labore et dolore magna aliqua. Quis ipsum suspendisse ultrices gravida. Risus commodo viverra maecenas accumsan lacus vel facilisis. Lorem ipsum dolor sit amet, consectetur adipiscing elit, sed do eiusmod tempor incididunt ut labore et dolore magna aliqua. Quis ipsum suspendisse ultrices gravida. Risus commodo viverra maecenas accumsan lacus vel facilisis. Lorem ipsum dolor sit amet, consectetur adipiscing elit, sed do eiusmod tempor incididunt ut labore et doLorem ipsum dolor sit amet, consectetur adipiscing elit, sed do eiusmod tempor incididunt ut labore et dolore magna aliqua. Quis ipsum suspendisse ultrices gravida. Risus commodo viverra maecenas accumsan lacus vel facilisis. Lorem ipsum dolor sit amet, consectetur adipiscing elit, sed do eiusmod tempor incididunt ut labore et dolore magna aliqua. Quis ipsum suspendisse ultrices gravida. Risus</p>
<div class="pill" style="left:110px;top:1982px;width:137px">READ MORE</div>
<div class="round-photo" role="img" aria-label="Photo of two businessmen looking at a tablet" style="left:683px;top:1464px;width:406px;height:406px;background:linear-gradient(135deg,#e9e4dc,#8a8e96 60%,#3c3f46)"></div>

<div class="bar" style="left:600px;top:2182px;width:347px"></div>
<h2 class="section-title" style="left:596px;top:2200px;font-size:40px">MEET THE HOSTS</h2>
<p class="hosts-text">Lorem ipsum dolor sit amet, consectetur adipiscing elit, sed do eiusmod tempor incididunt ut labore et dolore magna aliqua. Quis ipsum suspendisse ultrices gravida. Risus commodo viverra maecenas accumsan lacus vel facilisis. Lorem ipsum dolor sit amet, consectetur adipiscing elit, sed do eiusmod tempor incididunt ut labore et dolore magna aliqua. Quis ipsum suspendisse ultrices gravida. Risus commodo viverra maecenas accumsan lacus vel facilisis. Lorem ipsum dolor sit amet, consectetur adipiscing elit, sed do eiusmod tempor</p>
<div class="pill" style="left:598px;top:2539px;width:137px">READ MORE</div>
<div class="round-photo" role="img" aria-label="Photo of a smiling host speaking at a desk" style="left:111px;top:2213px;width:338px;height:338px;background:linear-gradient(135deg,#e6ece9,#c8d0d4 55%,#9a8a74)"></div>

<section class="newsletter">
  <div class="abs" role="img" aria-label="Dark photo of a desk with laptops" style="inset:0"></div>
  <h2>Lorem ipsum dolor sit amet, consectetur adipiscing elit, sed do eiusmod tempor incididunt</h2>
  <div class="field input" style="left:119px;width:95px">First Name</div>
  <div class="field input" style="left:231px;width:117px">Email Address</div>
  <div class="field submit" style="left:366px;width:123px">Download</div>
</section>
<div class="logo-panel">Bright<br>Gatherings</div>

<div class="bar" style="left:454px;top:3074px;width:279px"></div>
<h2 class="section-title" style="left:0;top:3090px;width:1200px;text-align:center;font-size:41px">TESTIMONIALS</h2>

<article class="testimonial" style="left:111px">
  <div class="stars">★★★★☆</div>
  <div class="quote">“</div>
  <p>Lorem ipsum dolor sit amet, consectetur adipiscing elit, sed do eiusmod tempor incididunt ut labore et dolore magna aliqua. Quis ipsum suspendisse ultrices gravida. Risus commodo viverra maecenas accumsan lacus vel facilisis. Lorem ipsum dolor sit amet, consectetur adipiscing elit, sed do eiusmod tempor incididunt ut labore et dolore magna</p>
  <svg class="tail" width="36" height="28" viewBox="0 0 36 28"><path d="M0 0 H36 L26 28 Z" fill="#f0581f"/></svg>
</article>
<article class="testimonial" style="left:600px">
  <div class="stars">★★★★☆</div>
  <div class="quote">“</div>
  <p>Lorem ipsum dolor sit amet, consectetur adipiscing elit, sed do eiusmod tempor incididunt ut labore et dolore magna aliqua. Quis ipsum suspendisse ultrices gravida. Risus commodo viverra maecenas accumsan lacus vel facilisis. Lorem ipsum dolor sit amet, consectetur adipiscing elit, sed do eiusmod tempor incididunt ut labore et dolore magna</p>
  <svg class="tail" width="36" height="28" viewBox="0 0 36 28"><path d="M0 0 H36 L26 28 Z" fill="#f0581f"/></svg>
</article>

<footer class="site-footer"></footer>
<div class="footer-logo">Bright<br>Gatherings</div>
<nav class="footer-nav">
  <a style="left:261px">Home</a><i style="left:360px"></i>
  <a style="left:383px">About us</a><i style="left:517px"></i>
  <a style="left:543px">services</a><i style="left:672px"></i>
  <a style="left:697px">Blog</a><i style="left:778px"></i>
  <a style="left:803px">Contact us</a>
</nav>
<p class="footer-note">Lorem ipsum dolor sit amet, consectetur adipiscing elit, sed do eiusmod tempor incididunt ut labore et dolore magna aliqua. Quis ipsum suspendisse ultrices</p>
<p class="copyright">@copyrights bright gatherings 2019.All rights reserved</p>

</body>
</html>
```